Whitcombe Business Card Design

The name of the business is Dario Whitcombe, CPA LLC
The service that we offer is Accounting, Tax & Consulting Services. I need it to have the following items:
Dario Whitcombe, Principal
Phone Number
Email Address
Physical Address

I have attached the company logo, one in black and one in white. Please provide a design in black background and the other in white background. Please include "Accounting, Tax & Consulting Services". I want the business card to be clean and very professional.

```html
<!DOCTYPE html>
<html lang="en">
<head>
<meta charset="utf-8">
<title>Dario Whitcombe, CPA LLC – Business Cards</title>
<link rel="stylesheet" href="https://fonts.googleapis.com/css2?family=Poppins:wght@400;500;600;700&display=swap">
<style>
  :root {
    --stage: #2b2b2d;
    --card-black: #0a0a0a;
    --brand-red: #9b161b;
    --brand-red-deep: #8a1217;
    --white: #ffffff;
    --grey: #a7a7a9;
    --card-w: 760px;
    --card-h: 434px;
  }
  * { box-sizing: border-box; margin: 0; padding: 0; }
  html, body {
    width: 1200px; height: 1015px; overflow: hidden;
    background: var(--stage);
    font-family: "Poppins", sans-serif;
  }
  .card {
    position: absolute; left: 220px;
    width: var(--card-w); height: var(--card-h);
    background: var(--card-black);
    overflow: hidden;
    box-shadow: 0 14px 30px rgba(0,0,0,.45);
  }
  .card--front { top: 55px; }
  .card--back { top: 526px; }

  /* Front */
  .front-lockup {
    position: absolute; top: 118px; left: 0; right: 0;
    display: flex; flex-direction: column; align-items: center;
  }
  .brand-square {
    width: 54px; height: 54px; border: 6px solid var(--white);
    margin-bottom: 22px;
  }
  .brand-name {
    color: var(--white); font-weight: 600; font-size: 34px;
    letter-spacing: 1px; text-transform: uppercase; line-height: 1.1;
  }
  .brand-descriptor {
    color: var(--grey); font-weight: 500; font-size: 18px;
    letter-spacing: 4px; text-transform: uppercase; margin-top: 6px;
  }
  .service-band {
    position: absolute; left: 0; right: 0; bottom: 0; height: 92px;
    background: var(--brand-red);
    display: flex; align-items: center; justify-content: center;
    color: var(--white); font-weight: 500; font-size: 20px;
    text-transform: uppercase; letter-spacing: .5px;
  }

  /* Back */
  .back-header {
    position: absolute; top: 0; left: 0; right: 0; height: 150px;
    display: flex; align-items: center; gap: 30px; padding-left: 52px;
  }
  .back-header .brand-square { margin: 0; width: 64px; height: 64px; }
  .back-header .brand-name { font-size: 30px; }
  .back-header .brand-descriptor { font-size: 16px; letter-spacing: 3.5px; }
  .back-body {
    position: absolute; top: 150px; left: 0; right: 0; bottom: 0;
    background: var(--brand-red); color: var(--white);
    padding: 34px 0 0 146px;
    overflow: hidden;
  }
  .back-watermark {
    position: absolute; right: -40px; top: 10px;
    width: 260px; height: 260px;
    border: 34px solid var(--brand-red-deep);
  }
  .contact-block { position: relative; }
  .person-name { font-weight: 700; font-size: 28px; line-height: 1.1; }
  .person-role { font-weight: 400; font-size: 20px; line-height: 1.2; }
  .contact-list { list-style: none; margin-top: 22px; }
  .contact-item {
    display: flex; align-items: center; gap: 14px;
    font-size: 19px; line-height: 1.4;
  }
  .contact-icon { width: 24px; height: 24px; flex: none; }
  .address { margin-top: 14px; margin-left: 38px; font-size: 19px; line-height: 1.35; }
</style>
</head>
<body>
  <section class="card card--front" aria-label="Business card front">
    <div class="front-lockup">
      <div class="brand-square"></div>
      <div class="brand-name">Dario Whitcombe, CPA LLC</div>
      <div class="brand-descriptor">Certified Public Accountant</div>
    </div>
    <div class="service-band">Accounting, Tax &amp; Consulting Services</div>
  </section>

  <section class="card card--back" aria-label="Business card back">
    <header class="back-header">
      <div class="brand-square"></div>
      <div>
        <div class="brand-name">Dario Whitcombe, CPA LLC</div>
        <div class="brand-descriptor">Certified Public Accountant</div>
      </div>
    </header>
    <div class="back-body">
      <div class="back-watermark" aria-hidden="true"></div>
      <div class="contact-block">
        <div class="person-name">Dario Whitcombe</div>
        <div class="person-role">Principal</div>
        <ul class="contact-list">
          <li class="contact-item">
            <svg class="contact-icon" viewBox="0 0 24 24" fill="none" stroke="currentColor" stroke-width="2">
              <rect x="2" y="2" width="20" height="20" rx="2"/>
              <path d="M8 6c-1 1-1 3 1 6s5 5 7 5l1-2-3-2-1 1c-1-.5-2.5-2-3-3l1-1-2-3z" fill="currentColor" stroke="none"/>
            </svg>
            <span>055-208 317 642</span>
          </li>
          <li class="contact-item">
            <svg class="contact-icon" viewBox="0 0 24 24" fill="currentColor">
              <path d="M2 5h20v14H2z"/>
              <path d="M2 5l10 8 10-8" fill="none" stroke="#9b161b" stroke-width="2"/>
            </svg>
            <span>info@whitcombecpa.com</span>
          </li>
        </ul>
        <p class="address">421, Address line here<br>Country Name, 45452</p>
      </div>
    </div>
  </section>
</body>
</html>
```